Professional & attention grabbing.

A business card design, front and back. I already have a logo I will attach, but I am open to something new as well.
Things to include:
Name:
Title:
Phone:
Email:
Wanting something that is professional but attention grabbing.
Also we do a lot of work using drones on natural gas pipelines (leading the future)if you want to include any of that. I'm open to ideas.
Target Market(s)
Natural gas transmission industry / greenhouse gas mitigation industry
Industry/Entity Type
Business
Colors
Designer to choose colors to be used in the design.
Look and feel
Each slider illustrates characteristics of the customer's brand and the style your logo design should communicate.

```html
<!DOCTYPE html>
<html lang="en">
<head>
<meta charset="utf-8">
<title>Kestrel Inspections – Business Card</title>
<link href="https://fonts.googleapis.com/css2?family=Roboto:wght@400;700&display=swap" rel="stylesheet">
<style>
  :root {
    --stage: #5a5552;
    --card: #161616;
    --card-edge: #0d0d0d;
    --red: #c8202b;
    --white: #f2f2f2;
    --grey-text: #d6d6d6;
    --emboss: #6d6d6d;
    --rule: #8a8a8a;
  }
  * { box-sizing: border-box; margin: 0; padding: 0; }
  html, body {
    width: 1200px; height: 864px; overflow: hidden;
    background: var(--stage);
    font-family: "Roboto", Arial, sans-serif;
  }
  .stage {
    position: relative; width: 1200px; height: 864px;
    display: flex; align-items: center; justify-content: center; gap: 40px;
  }
  .card {
    position: relative; width: 540px; height: 308px;
    background: var(--card);
    box-shadow: 0 10px 24px rgba(0,0,0,.35);
  }
  /* Front */
  .card--front .brand {
    position: absolute; left: 120px; top: 96px;
    display: flex; align-items: center; gap: 14px;
  }
  .brand__square { width: 34px; height: 34px; background: var(--emboss); }
  .card--front .brand__name {
    font-weight: 700; font-size: 34px; color: var(--emboss); letter-spacing: 1px;
  }
  .card--front .website {
    position: absolute; left: 120px; top: 190px;
    font-size: 14px; letter-spacing: 5px; color: var(--emboss);
  }
  /* Back */
  .card--back .brand {
    position: absolute; right: 34px; top: 44px;
    display: flex; align-items: center; gap: 10px;
  }
  .card--back .brand__square { width: 26px; height: 26px; background: var(--red); }
  .card--back .brand__name {
    font-weight: 700; font-size: 24px; color: var(--white); letter-spacing: .5px;
  }
  .person { position: absolute; left: 34px; top: 118px; }
  .person__name { color: var(--red); font-size: 17px; font-weight: 400; letter-spacing: .5px; }
  .person__title { color: var(--white); font-size: 14px; margin-top: 2px; letter-spacing: .5px; }
  .person__rule { width: 120px; height: 1px; background: var(--rule); margin-top: 6px; }
  .contacts { position: absolute; left: 34px; top: 186px; list-style: none; }
  .contacts li {
    display: flex; align-items: center; gap: 10px;
    color: var(--grey-text); font-size: 13px; height: 20px;
  }
  .contacts svg { width: 12px; height: 12px; fill: var(--red); }
  .long-rule {
    position: absolute; left: 160px; right: 34px; top: 262px;
    height: 1px; background: var(--rule);
  }
</style>
</head>
<body>
<main class="stage">
  <section class="card card--front" aria-label="Card front">
    <div class="brand">
      <span class="brand__square"></span>
      <span class="brand__name">KESTREL INSPECTIONS</span>
    </div>
    <p class="website">www.example.com</p>
  </section>

  <section class="card card--back" aria-label="Card back">
    <div class="brand">
      <span class="brand__square"></span>
      <span class="brand__name">KESTREL INSPECTIONS</span>
    </div>
    <div class="person">
      <p class="person__name">EVAN MARSH</p>
      <p class="person__title">PRESIDENT</p>
      <div class="person__rule"></div>
    </div>
    <ul class="contacts">
      <li>
        <svg viewBox="0 0 12 12" aria-hidden="true"><path d="M2.5 1 4.3 3 3.4 4.3a7 7 0 0 0 4.3 4.3L9 7.7l2 1.8-1.4 1.8C5.5 11.1.9 6.5.7 2.4z"/></svg>
        555 0142 7788
      </li>
      <li>
        <svg viewBox="0 0 12 12" aria-hidden="true"><path d="M0 2h12v1.2L6 7 0 3.2z M0 4.6 6 8.4l6-3.8V10H0z"/></svg>
        evan@example.com
      </li>
      <li>
        <svg viewBox="0 0 12 12" aria-hidden="true"><circle cx="6" cy="6" r="6"/></svg>
        www.example.com
      </li>
    </ul>
    <div class="long-rule"></div>
  </section>
</main>
</body>
</html>
```